Professional Website for Leading Global Private Equity Real Estate Company

The company is a leading global Private Equity Real Estate (PERE). We need a homepage design, an inner page design, and color/font tweaks to the logo (color should be more soothing than current blue used in the logo). The logo website should project the company as global, professional, experienced, trustworthy, accessible, YOUNG, DYNAMIC, hi-tech. PLEASE SEE the attached Design Brief Word Doc for details.

Target Market(s)

institional investors and wealthy private individuals

Industry/Entity Type

Finance

Number of Pages Required

2 page

Font styles to use
Sans Serif
Other font styles liked:
• either like in https://www.ferndalequay.com/ or like in presentations (Montserrat Black & Montserrat Light, Century Gothic, Blair ITC, Almoni Neue DL 4.0 AAA Medium, Almoni DL AAA)

Requirements
Must have
• new color palette that is NOT based on current logo. they want a more soothing color palette than the blue in that logo. the new color palette should project: global, professional, experienced, trustworthy, accessible, YOUNG, DYNAMIC, hi-tech.
Nice to have
• the likes these sites: https://www.ferndalequay.com/ and https://www.tvr.law/

```html
<!DOCTYPE html>
<html lang="en">
<head>
<meta charset="utf-8">
<title>Veltria Real Estate</title>
<link href="https://fonts.googleapis.com/css2?family=Michroma&family=Montserrat:wght@300;400;500;600;700&family=Roboto:wght@300;400;500&display=swap" rel="stylesheet">
<style>
:root{
  --teal-deep:#123c48;
  --teal:#17495a;
  --teal-btn:#1a5466;
  --ink:#2b2b2b;
  --body:#4a4a4a;
  --grey-bg:#eeeeee;
  --line:#d8d8d8;
  --white:#ffffff;
  --head:"Michroma",sans-serif;
  --sans:"Montserrat",sans-serif;
  --text:"Roboto",sans-serif;
}
*{box-sizing:border-box;margin:0;padding:0}
html,body{width:1200px;height:3987px;overflow:hidden;background:var(--white)}
body{position:relative;font-family:var(--text);color:var(--body)}
.section{position:absolute;left:0;width:1200px;overflow:hidden}
.abs{position:absolute}
.h2{font-family:var(--head);color:var(--ink);font-size:30px;letter-spacing:1px;line-height:1.3;text-transform:uppercase}
.rule{position:absolute;height:3px;width:58px;background:var(--teal)}
.btn-outline{position:absolute;border:2px solid var(--teal);color:var(--teal);font-family:var(--sans);font-weight:600;font-size:11px;letter-spacing:1.5px;display:flex;align-items:center;justify-content:center;text-transform:uppercase}
.btn-solid{position:absolute;background:var(--teal);color:var(--white);font-family:var(--sans);font-weight:600;font-size:13px;letter-spacing:1.5px;display:flex;align-items:center;justify-content:center;text-transform:uppercase}
.para{font-size:14.5px;line-height:27px;color:var(--body)}

/* hero */
.hero{top:0;height:706px;background:radial-gradient(ellipse at 55% 45%,#5d6c8c 0%,#34456a 30%,#1b2746 60%,#0e1730 100%)}
.hero-glow{position:absolute;left:0;top:330px;width:1200px;height:376px;background:linear-gradient(180deg,rgba(0,0,0,0),rgba(180,110,50,.35) 55%,rgba(20,30,55,.6))}
.hero-shade{position:absolute;inset:0;background:rgba(10,20,40,.25)}
.nav{position:absolute;top:0;left:0;width:1200px;height:78px;background:rgba(12,24,48,.55)}
.brand{position:absolute;left:100px;top:14px;display:flex;align-items:center;gap:10px;color:var(--white);font-family:var(--sans)}
.brand-dot{width:44px;height:44px;border-radius:50%;background:var(--white)}
.brand-name{font-weight:500;font-size:18px;line-height:22px;letter-spacing:1px}
.nav-links{position:absolute;left:356px;top:35px;display:flex;gap:32px;font-family:var(--sans);font-weight:500;font-size:13px;color:var(--white);letter-spacing:.3px}
.login{position:absolute;left:1003px;top:25px;width:112px;height:34px;background:var(--teal-btn);color:var(--white);font-family:var(--sans);font-size:13px;display:flex;align-items:center;justify-content:center}
.hero-title{position:absolute;top:300px;left:0;width:1200px;text-align:center;font-family:var(--head);color:var(--white);font-size:39px;line-height:44px;letter-spacing:1.5px}
.hero-btn{position:absolute;left:526px;top:402px;width:188px;height:47px;border:2px solid var(--white);color:var(--white);font-family:var(--sans);font-size:15px;letter-spacing:2px;display:flex;align-items:center;justify-content:center}
.stats-line{position:absolute;top:609px;left:0;width:1200px;height:1px;background:rgba(255,255,255,.45)}
.stat{position:absolute;top:604px;width:240px;text-align:center;color:var(--white)}
.stat::before{content:"";display:block;margin:0 auto 16px;width:10px;height:10px;border-radius:50%;background:var(--white)}
.stat-val{font-family:var(--head);font-size:29px;line-height:32px}
.stat-lbl{font-family:var(--sans);font-size:15px;margin-top:4px}

/* about */
.about{top:706px;height:385px}
.eyebrow{font-family:var(--sans);font-size:14px;color:#888;letter-spacing:.5px}

/* platforms */
.platforms{top:1091px;height:511px;background:var(--grey-bg)}
.card{position:absolute;width:212px;text-align:center}
.card.active{background:var(--white);border-bottom:3px solid var(--teal);box-shadow:0 2px 8px rgba(0,0,0,.08);height:284px}
.card svg{display:block;margin:0 auto}
.card-title{font-family:var(--sans);font-weight:700;font-size:11px;color:var(--ink);margin-top:10px;line-height:14px;letter-spacing:.3px}
.card-text{font-size:10.5px;line-height:14px;color:#666;margin:8px auto 0;width:170px}
.card-btn{margin:12px auto 0;width:114px;height:29px;border:2px solid var(--teal);color:var(--teal);font-family:var(--sans);font-weight:600;font-size:9.5px;letter-spacing:1px;display:flex;align-items:center;justify-content:center}

/* edge */
.edge{top:1602px;height:554px}
.edge-photo{position:absolute;left:0;top:0;width:596px;height:554px;background:linear-gradient(160deg,#e8eef5 0%,#b9cde2 35%,#6f90b5 62%,#2f4d73 100%)}

/* subscribe */
.stay{top:2156px;height:386px;background:linear-gradient(180deg,#2a5262 0%,#1b4250 55%,#15384a 100%)}
.stay-title{position:absolute;top:112px;width:1200px;text-align:center;font-family:var(--head);font-size:28px;color:var(--white);letter-spacing:2px}
.stay-sub{position:absolute;top:158px;width:1200px;text-align:center;font-size:16px;color:var(--white)}
.field{position:absolute;background:var(--white);border:1px solid #ccc;font-family:var(--sans);font-size:11px;color:#555;padding-left:19px;display:flex;align-items:center}
.subscribe{position:absolute;left:831px;top:208px;width:197px;height:51px;background:#2a6677;color:var(--white);font-family:var(--head);font-size:16px;letter-spacing:1.5px;display:flex;align-items:center;justify-content:center}

/* responsibility */
.resp{top:2542px;height:546px}
.resp-photo{position:absolute;left:131px;top:63px;width:418px;height:418px;border-radius:50%;background:radial-gradient(circle at 45% 45%,#d9d9d9,#9a9a9a 60%,#555 100%)}

/* contact */
.contact{top:3088px;height:516px;background:var(--grey-bg)}
.contact-photo{position:absolute;left:604px;top:0;width:596px;height:516px;background:linear-gradient(135deg,#c7b39a 0%,#8c7a66 40%,#5f5a58 70%,#3c3a3d 100%)}
.cfield{border:1px solid #e2e2e2;align-items:flex-start;padding-top:0}

/* footer */
.footer{top:3604px;height:383px}
.f-head{position:absolute;top:60px;font-family:var(--text);font-size:15px;color:var(--teal);font-weight:500}
.f-head::after{content:"";display:block;width:62px;height:2px;background:var(--teal);margin-top:5px}
.f-list{position:absolute;top:102px;list-style:none;font-size:13px;line-height:27px;color:var(--teal)}
.f-contact{position:absolute;left:846px;font-size:13px;color:var(--teal);display:flex;gap:14px;align-items:flex-start;line-height:16px}
.ic{width:26px;height:26px;border-radius:50%;background:var(--teal);flex:none;display:flex;align-items:center;justify-content:center}
.social{position:absolute;left:852px;top:236px;display:flex;gap:7px}
.social span{width:27px;height:27px;border-radius:50%;background:#b5b5b5}
.social span:first-child{background:var(--teal)}
.f-rule{position:absolute;top:308px;left:0;width:1200px;height:1px;background:var(--line)}
.copy{position:absolute;top:333px;left:113px;font-size:12px;color:var(--teal)}
.legal{position:absolute;top:333px;right:135px;font-size:12px;color:var(--teal)}
</style>
</head>
<body>

<section class="section hero">
  <div role="img" aria-label="Night aerial view of a city skyline with illuminated towers" class="abs" style="inset:0"></div>
  <div class="hero-glow"></div>
  <div class="hero-shade"></div>
  <header class="nav">
    <div class="brand"><span class="brand-dot"></span><span class="brand-name">VELTRIA<br>REAL ESTATE</span></div>
    <nav class="nav-links"><span>ABOUT US ⌄</span><span>OUR BUSINESSES ⌄</span><span>INVESTORS LOBBY</span><span>NEWS</span><span>CONTACT US</span></nav>
    <div class="login">LOG IN</div>
  </header>
  <svg class="abs" style="left:572px;top:234px" width="54" height="54" viewBox="0 0 54 54"><circle cx="27" cy="27" r="25" fill="none" stroke="#fff" stroke-width="2"/><path d="M21 16 L38 27 L21 38 Z" fill="#fff"/></svg>
  <h1 class="hero-title">LEADING GLOBAL PRIVATE<br>EQUITY REAL ESTATE</h1>
  <div class="hero-btn">ABOUT US</div>
  <div class="stats-line"></div>
  <div class="stat" style="left:147px"><div class="stat-val">$250</div><div class="stat-lbl">REAL ESTATE PROJECTS</div></div>
  <div class="stat" style="left:417px"><div class="stat-val">$25B</div><div class="stat-lbl">PRIVATE EQUITY</div></div>
  <div class="stat" style="left:645px"><div class="stat-val">$13B</div><div class="stat-lbl">FUND SOLUTIONS</div></div>
  <div class="stat" style="left:894px"><div class="stat-val">$10B</div><div class="stat-lbl">PRIVATE EQUITY</div></div>
</section>

<section class="section about">
  <div class="abs eyebrow" style="left:141px;top:97px">WHO WE ARE</div>
  <h2 class="abs h2" style="left:139px;top:118px">ABOUT VELTRIA<br>REAL ESTATE</h2>
  <div class="rule" style="left:141px;top:203px"></div>
  <div class="btn-outline" style="left:141px;top:235px;width:156px;height:38px">LEARN MORE</div>
  <p class="abs para" style="left:551px;top:114px;width:520px;font-size:15.5px">Lorem ipsum dolor sit amet, consectetur adipiscing elit, sed do eius­mod tempor incididunt ut labore et doloreUt enim ad minim veniam, quis nostrud exercitation ullamco laboris nisi ut aliquip ex ea Lorem ipsum dolor sit amet, consectetur adipiscing elitLorem ipsum dolor sit amet, consectetur adipiscing elit sed.</p>
</section>

<section class="section platforms">
  <h2 class="abs h2" style="left:0;top:48px;width:1200px;text-align:center;font-size:26px">OUR INVESTMENT PLATFORMS</h2>
  <div class="rule" style="left:560px;top:89px;width:58px"></div>

  <div class="card" style="left:55px;top:162px">
    <svg width="96" height="96" viewBox="0 0 96 96"><circle cx="48" cy="48" r="42" fill="none" stroke="#17495a" stroke-width="8"/><circle cx="48" cy="44" r="12" fill="none" stroke="#17495a" stroke-width="2"/><rect x="43" y="58" width="10" height="6" fill="#17495a"/></svg>
    <div class="card-title">SED UT PERSPICIATIS<br>UNDE OMNIS</div>
    <div class="card-text">Lorem ipsum dolor sit amet, consectetur adipiscing elit, sed do eiusmod</div>
    <div class="card-btn">LEARN MORE</div>
  </div>
  <div class="card active" style="left:285px;top:147px;padding-top:23px">
    <svg width="96" height="96" viewBox="0 0 96 96"><circle cx="48" cy="48" r="42" fill="none" stroke="#17495a" stroke-width="8"/><rect x="32" y="34" width="32" height="20" fill="none" stroke="#17495a" stroke-width="2"/><circle cx="40" cy="62" r="4" fill="#17495a"/><circle cx="56" cy="62" r="4" fill="#17495a"/></svg>
    <div class="card-title">SED UT PERSPICIATIS<br>UNDE OMNIS</div>
    <div class="card-text">Lorem ipsum dolor sit amet, consectetur adipiscing elit, sed do eiusmod</div>
    <div class="card-btn">LEARN MORE</div>
  </div>
  <div class="card" style="left:509px;top:166px">
    <svg width="96" height="96" viewBox="0 0 96 96"><circle cx="48" cy="48" r="42" fill="none" stroke="#17495a" stroke-width="8"/><rect x="34" y="52" width="6" height="12" fill="#17495a"/><rect x="44" y="46" width="6" height="18" fill="#17495a"/><rect x="54" y="40" width="6" height="24" fill="#17495a"/><path d="M32 46 L46 36 L54 40 L64 30" fill="none" stroke="#17495a" stroke-width="2"/></svg>
    <div class="card-title">SED UT PERSPICIATIS<br>UNDE OMNIS</div>
    <div class="card-text">Lorem ipsum dolor sit amet, consectetur adipiscing elit, sed do eiusmod</div>
    <div class="card-btn">LEARN MORE</div>
  </div>
  <div class="card" style="left:730px;top:162px">
    <svg width="96" height="96" viewBox="0 0 96 96"><circle cx="48" cy="48" r="42" fill="none" stroke="#17495a" stroke-width="8"/><rect x="38" y="30" width="14" height="34" fill="none" stroke="#17495a" stroke-width="2"/><rect x="52" y="42" width="10" height="22" fill="none" stroke="#17495a" stroke-width="2"/></svg>
    <div class="card-title">SED UT PERSPICIATIS<br>UNDE OMNIS</div>
    <div class="card-text">Lorem ipsum dolor sit amet, consectetur adipiscing elit, sed do eiusmod</div>
    <div class="card-btn">LEARN MORE</div>
  </div>
  <div class="card" style="left:945px;top:155px">
    <svg width="96" height="96" viewBox="0 0 96 96"><circle cx="48" cy="48" r="42" fill="none" stroke="#17495a" stroke-width="8"/><rect x="32" y="34" width="32" height="22" fill="none" stroke="#17495a" stroke-width="2"/><rect x="38" y="44" width="4" height="8" fill="#17495a"/><rect x="45" y="40" width="4" height="12" fill="#17495a"/><rect x="52" y="46" width="4" height="6" fill="#17495a"/><path d="M42 62 H54" stroke="#17495a" stroke-width="2"/></svg>
    <div class="card-title">SED UT PERSPICIATIS<br>UNDE OMNIS</div>
    <div class="card-text">Lorem ipsum dolor sit amet, consectetur adipiscing elit, sed do eiusmod</div>
    <div class="card-btn">LEARN MORE</div>
  </div>
</section>

<section class="section edge">
  <div class="edge-photo" role="img" aria-label="Glass office tower seen from below against a cloudy blue sky"></div>
  <h2 class="abs h2" style="left:673px;top:102px;font-size:31px">OUR EDGE</h2>
  <div class="rule" style="left:675px;top:148px"></div>
  <p class="abs para" style="left:673px;top:176px;width:460px">Lorem ipsum dolor sit amet, consectetur adipiscing elit, sed do eiusmod tempor incididunt ut co laboris nisi ut aliquip ex ea com­modo consequat. Duis aute irure dolor in reprehende</p>
  <p class="abs para" style="left:673px;top:270px;width:460px">Aabor et dolore magna aliqua. Ut enim ad minim veniam, quis nostrud exercitation ullamco laboris nisi ut aliquip ex ea commodo consequat. Duis aute irure dolor in reprehenderitd exercitation</p>
  <div class="btn-solid" style="left:672px;top:387px;width:272px;height:53px">INVESTOR INFORMATION</div>
</section>

<section class="section stay" role="img" aria-label="Dimmed teal-toned city skyline behind the newsletter signup">
  <div class="stay-title">STAY UPDATED</div>
  <div class="stay-sub">Get our latest insights, firm announcements and Charitable Foundation updates.</div>
  <div class="field" style="left:201px;top:208px;width:305px;height:51px">NAME*</div>
  <div class="field" style="left:515px;top:208px;width:305px;height:51px">EMAIL*</div>
  <div class="subscribe">SUBSCRIBE</div>
</section>

<section class="section resp">
  <div class="resp-photo" role="img" aria-label="Black and white photo of colleagues working together at a desk, cropped in a circle"></div>
  <h2 class="abs h2" style="left:635px;top:128px;font-size:29px">OUR RESPONSIBILITY</h2>
  <div class="rule" style="left:640px;top:170px"></div>
  <p class="abs para" style="left:636px;top:198px;width:430px;font-size:14px;line-height:24px">Lorem ipsum dolor sit amet, consectetur adipiscing elit, sed do eiusmod tempor incididunt ut</p>
  <p class="abs para" style="left:636px;top:260px;width:430px;font-size:14px;line-height:24px">Aabor et dolore magna aliqua. Ut enim ad minim veniam, quis nostrud exercitation ullamco laboris nisi ut aliquip ex ea com­modo consequat. Duis aute irure dolor in reprehenderitd exer­citationa aliqua. Ut enim ad minim veniam.</p>
  <div class="btn-outline" style="left:638px;top:364px;width:167px;height:45px;font-size:12px">LEARN MORE</div>
</section>

<section class="section contact">
  <div class="abs eyebrow" style="left:118px;top:79px;color:#666">CONTACT US</div>
  <h2 class="abs h2" style="left:116px;top:96px;font-size:29px">GET IN TOUCH</h2>
  <div class="rule" style="left:118px;top:139px;width:36px;height:2px"></div>
  <div class="field cfield" style="left:115px;top:158px;width:215px;height:39px;align-items:center">First Name</div>
  <div class="field cfield" style="left:337px;top:158px;width:216px;height:39px;align-items:center">Last Name</div>
  <div class="field cfield" style="left:115px;top:205px;width:215px;height:38px;align-items:center">Phone Number</div>
  <div class="field cfield" style="left:337px;top:205px;width:216px;height:38px;align-items:center">Email address</div>
  <div class="field cfield" style="left:115px;top:253px;width:438px;height:75px;padding-top:14px">Message</div>
  <div class="btn-solid" style="left:115px;top:349px;width:207px;height:43px;font-size:12px">SUBMIT MESSAGE</div>
  <div class="contact-photo" role="img" aria-label="Three smiling colleagues meeting around a laptop in a bright office"></div>
</section>

<footer class="section footer">
  <div class="f-head" style="left:124px">IMPORTANT LINKS</div>
  <ul class="f-list" style="left:124px"><li>About Us</li><li>Our Businesses</li><li>Investor Lobby</li><li>News</li><li>Contact Us</li></ul>
  <div class="f-head" style="left:350px">EXPLORE VELTRIA REAL ESTATE</div>
  <ul class="f-list" style="left:352px"><li>Private Equity</li><li>Real Estate</li><li>Credit</li><li>Strategic Partners</li><li>Tactical Opportunities</li><li>Infrastructure</li></ul>
  <ul class="f-list" style="left:555px"><li>Insurance Solutions</li><li>Life Sciences</li><li>Portfolio Operations</li><li>Technology and Innovations</li><li>Registered Products</li></ul>
  <div class="f-head" style="left:843px">CONTACT DETAILS</div>
  <div class="f-contact" style="top:100px"><span class="ic"><svg width="12" height="14" viewBox="0 0 12 14"><path d="M6 0a5 5 0 0 1 5 5c0 4-5 9-5 9S1 9 1 5a5 5 0 0 1 5-5z" fill="#fff"/><circle cx="6" cy="5" r="2" fill="#17495a"/></svg></span><span>72 Harbor Point Dr Suite B<br>Cedar Bay, FL <small>33910</small></span></div>
  <div class="f-contact" style="top:144px;align-items:center"><span class="ic"><svg width="12" height="12" viewBox="0 0 12 12"><path d="M2 1l2 0 1 3-1.5 1a7 7 0 0 0 3.5 3.5L8 7l3 1v2c0 1-1 1-1 1C5 11 1 7 1 2c0 0 0-1 1-1z" fill="#fff"/></svg></span><span style="font-size:14px">555-014-2281</span></div>
  <div class="f-contact" style="top:179px;align-items:center"><span class="ic"><svg width="13" height="10" viewBox="0 0 13 10"><rect x="0.5" y="0.5" width="12" height="9" fill="none" stroke="#fff"/><path d="M1 1l5.5 4.5L12 1" fill="none" stroke="#fff"/></svg></span><span>info@veltriarealestate.com</span></div>
  <div class="social"><span></span><span></span><span></span><span></span></div>
  <div class="f-rule"></div>
  <div class="copy">Copyright © 2022 Veltria Realestate</div>
  <div class="legal">Terms of Use &nbsp;|&nbsp; Sitemap &nbsp;|&nbsp; Privacy Policy</div>
</footer>

</body>
</html>
```